Looking for someone to design a business card for my plumbing business Quandor Plumbing Solutions I want the background also to be black, must attract clients. If possible I want the front to be the logo and the back to show maybe the details.

Target Market(s)

Clients

Industry/Entity Type

Plumbing maintenance

Contact Information for Business Card

Name: Felix, Contact: 0461 539 207, Email: quandorplumbingsolutions@mailbrook.example, Licence number 728093K

Font styles to use
Other font styles liked:
• as per logo maybe?

Colors

Designer to choose colors to be used in the design.

Requirements
Nice to have
• stating the service I provide, emergency plumbing, plumbing maintenance, drainage maintenance, block sewer and stormwater, camera and locating.

```html
<!DOCTYPE html>
<html lang="en">
<head>
<meta charset="utf-8">
<title>Quandor Plumbing Solutions – Business Card</title>
<link rel="stylesheet" href="https://fonts.googleapis.com/css2?family=Raleway:wght@500;600;700;800&display=swap">
<style>
  :root {
    --canvas-bg: #5e5e5e;
    --card-bg: #1f1f20;
    --ink: #f2f2f2;
    --ink-soft: #d9d9d9;
    --accent: #4a8fd6;
  }
  * { box-sizing: border-box; margin: 0; padding: 0; }
  html, body {
    width: 1200px;
    height: 875px;
    overflow: hidden;
    background: var(--canvas-bg);
    font-family: "Raleway", Arial, sans-serif;
  }
  .stage {
    width: 1200px;
    height: 875px;
    display: flex;
    align-items: center;
    justify-content: center;
    gap: 40px;
  }
  .card {
    width: 540px;
    height: 330px;
    background: var(--card-bg);
    border-radius: 22px;
    position: relative;
    color: var(--ink);
    box-shadow: 0 18px 40px rgba(0,0,0,0.35);
  }

  /* Front */
  .card-front {
    display: flex;
    flex-direction: column;
    align-items: center;
    justify-content: center;
  }
  .brand {
    display: flex;
    align-items: center;
    gap: 12px;
  }
  .brand-dot {
    width: 18px;
    height: 18px;
    border-radius: 50%;
    background: var(--accent);
    flex: none;
  }
  .brand-name {
    font-weight: 800;
    color: var(--accent);
    text-transform: uppercase;
    line-height: 1.05;
  }
  .card-front .brand-name { font-size: 34px; }
  .services {
    margin-top: 44px;
    text-align: center;
    font-size: 13.5px;
    font-weight: 500;
    line-height: 1.7;
    color: var(--ink);
  }
  .services .sep {
    color: var(--accent);
    margin: 0 6px;
  }

  /* Back */
  .card-back {
    display: flex;
    align-items: center;
    padding: 0 34px 0 40px;
  }
  .card-back .brand { width: 210px; }
  .card-back .brand-name { font-size: 21px; }
  .card-back .brand-dot { width: 13px; height: 13px; }
  .divider {
    width: 2px;
    height: 170px;
    background: var(--accent);
    margin: 0 22px;
    flex: none;
  }
  .details { font-size: 12.5px; font-weight: 500; color: var(--ink); }
  .person-name {
    font-size: 22px;
    font-weight: 800;
    color: var(--accent);
    text-transform: uppercase;
    letter-spacing: 0.5px;
  }
  .person-role { margin-top: 2px; font-size: 13px; }
  .licence { margin-top: 6px; margin-bottom: 12px; font-size: 13px; }
  .contact-list { list-style: none; }
  .contact-list li {
    display: flex;
    align-items: center;
    gap: 7px;
    margin-top: 5px;
    white-space: nowrap;
  }
  .contact-list svg { width: 11px; height: 11px; flex: none; fill: var(--accent); }
  .social-dot {
    width: 11px; height: 11px; border-radius: 50%;
    background: var(--accent); flex: none;
  }
  .email { font-size: 11px; }
</style>
</head>
<body>
  <main class="stage">
    <section class="card card-front" aria-label="Card front">
      <div class="brand">
        <span class="brand-dot"></span>
        <span class="brand-name">Quandor<br>Plumbing Solutions</span>
      </div>
      <p class="services">
        Emergency plumbing<span class="sep">•</span>Plumbing maintenance<span class="sep">•</span>Drainage maintenance<br>
        Block sewer and stormwater<span class="sep">•</span>Camera and locating
      </p>
    </section>

    <section class="card card-back" aria-label="Card back">
      <div class="brand">
        <span class="brand-dot"></span>
        <span class="brand-name">Quandor<br>Plumbing Solutions</span>
      </div>
      <div class="divider"></div>
      <div class="details">
        <p class="person-name">Felix</p>
        <p class="person-role">Founder &amp; CEO</p>
        <p class="licence">Licence number 728093K</p>
        <ul class="contact-list">
          <li>
            <svg viewBox="0 0 24 24" aria-hidden="true"><path d="M6.6 10.8a15.1 15.1 0 0 0 6.6 6.6l2.2-2.2a1 1 0 0 1 1-.25 11.4 11.4 0 0 0 3.6.57 1 1 0 0 1 1 1V20a1 1 0 0 1-1 1A17 17 0 0 1 3 4a1 1 0 0 1 1-1h3.5a1 1 0 0 1 1 1c0 1.25.2 2.45.57 3.57a1 1 0 0 1-.25 1z"/></svg>
            0461 539 207
          </li>
          <li class="email">
            <svg viewBox="0 0 24 24" aria-hidden="true"><path d="M2 5h20v14H2z M4 7v.5l8 5 8-5V7l-8 5z" fill-rule="evenodd"/></svg>
            quandorplumbingsolutions@mailbrook.example
          </li>
          <li>
            <span class="social-dot"></span>
            @QuandorPlumbingSolutions
          </li>
        </ul>
      </div>
    </section>
  </main>
</body>
</html>
```